Bridal show post card design

our company contracts hotels near airports and cruise ports. We sell hotel packages including one night stay at a hotel (before or after the trip) including parking while they are away and transfers to and from the airport or cruise port. we are marketing to the public for the first time (typically it's travel agents). Specifically doing a Bridal show. Below are the photos that will appear in our booth or on our banners etc. We would like a post card to reflect the stress of not booking a hotel with us ... instead they could start their honeymoon or vacation a day early, stay at the hotel and relax... avoiding the stress of getting to the airport or cruise port in time otherwise missing the boat or the flight. We would also like to include a $20 off savings on the post card.
Hotel

```html
<!DOCTYPE html>
<html lang="en">
<head>
<meta charset="utf-8">
<title>Harborgate Stay &amp; Park Getaways – Postcard</title>
<link rel="stylesheet" href="https://fonts.googleapis.com/css2?family=Oswald:wght@400;600;700&family=Open+Sans:wght@400;600&display=swap">
<style>
  :root {
    --header-grey: #d8d9db;
    --navy: #1f2c66;
    --band-green: #6b9a45;
    --band-green-dark: #557d34;
    --icon-tint: #c9ddb6;
    --offer-red: #d52a2e;
    --ink-dark: #333;
    --white: #fff;
  }
  * { margin: 0; padding: 0; box-sizing: border-box; }
  html, body { width: 1200px; height: 953px; overflow: hidden; background: var(--white); }
  .postcard { position: relative; width: 1200px; height: 953px; background: var(--white); overflow: hidden; }

  .masthead {
    position: absolute; left: 0; top: 0; width: 1200px; height: 200px;
    background: var(--header-grey);
    display: flex; flex-direction: column; align-items: center; justify-content: center;
    font-family: "Oswald", sans-serif; color: var(--navy);
  }
  .brand-name { font-size: 50px; font-weight: 600; letter-spacing: 1px; line-height: 1.1; }
  .brand-phone { font-size: 28px; font-weight: 600; letter-spacing: 2px; margin-top: 8px; }

  .photo-strip { position: absolute; left: 0; top: 200px; width: 1200px; height: 290px; background: var(--white); }
  .photo { position: absolute; top: 0; height: 290px; }
  .photo-shuttle { left: 0; width: 310px; clip-path: polygon(0 0, 100% 0, 88% 100%, 0 100%);
    background: linear-gradient(160deg, #1b1b1e 0%, #3a2a15 45%, #c8741c 70%, #2a2320 100%); }
  .photo-couple { left: 278px; width: 330px; clip-path: polygon(10% 0, 100% 0, 91% 100%, 0 100%);
    background: linear-gradient(180deg, #5c7fae 0%, #c9a486 50%, #f1a443 75%, #6b4a3a 100%); }
  .photo-relax { left: 580px; width: 330px; clip-path: polygon(9% 0, 100% 0, 91% 100%, 0 100%);
    background: linear-gradient(135deg, #e3c9a4 0%, #c9a67c 50%, #b48d62 100%); }
  .photo-beach { left: 882px; width: 318px; clip-path: polygon(9% 0, 100% 0, 100% 100%, 0 100%);
    background: linear-gradient(180deg, #5f9ed8 0%, #a9cdee 45%, #eef3f6 70%, #c9d3da 100%); }

  .services-band {
    position: absolute; left: 0; top: 490px; width: 1200px; height: 210px;
    background: var(--band-green);
    display: grid; grid-template-columns: 120px repeat(4, 255px) 60px;
  }
  .service {
    grid-row: 1; display: flex; flex-direction: column; align-items: center;
    padding-top: 22px; color: var(--white); text-align: center;
  }
  .service:nth-child(1) { grid-column: 2; }
  .service:nth-child(2) { grid-column: 3; }
  .service:nth-child(3) { grid-column: 4; }
  .service:nth-child(4) { grid-column: 5; }
  .service-icon { height: 70px; width: 150px; }
  .service-title { font-family: "Open Sans", sans-serif; font-size: 30px; font-weight: 400; margin-top: 4px; line-height: 1.1; }
  .service-note { font-family: "Open Sans", sans-serif; font-size: 19px; line-height: 1.25; margin-top: 2px; }

  .rule { position: absolute; left: 0; top: 708px; width: 1200px; height: 8px; background: var(--navy); }

  .offer {
    position: absolute; left: 20px; top: 732px; width: 980px; text-align: center;
    font-family: "Oswald", sans-serif; color: var(--offer-red); white-space: nowrap;
  }
  .offer-headline { font-size: 56px; font-weight: 700; line-height: 1.15; letter-spacing: 0.5px; }
  .offer-sub { font-size: 40px; font-weight: 400; line-height: 1.15; margin-top: 4px; }
  .offer-terms { font-family: "Open Sans", sans-serif; font-size: 16px; font-weight: 600; color: var(--ink-dark); margin-top: 8px; line-height: 1.2; }

  .travel-graphic {
    position: absolute; left: 1010px; top: 724px; width: 176px; height: 206px; border-radius: 18px;
    background: radial-gradient(circle at 70% 65%, #3f8fd0 0%, #7cc0ea 35%, transparent 60%),
                linear-gradient(160deg, #6dbb3d 0%, #b9dd8e 40%, #d9e4ee 70%, #8fa6bd 100%);
  }
</style>
</head>
<body>
<main class="postcard">
  <header class="masthead">
    <div class="brand-name">Harborgate Stay &amp; Park Getaways</div>
    <div class="brand-phone">800-555-0142</div>
  </header>

  <section class="photo-strip">
    <div class="photo photo-shuttle" role="img" aria-label="Illuminated airport shuttle sign at night"></div>
    <div class="photo photo-couple" role="img" aria-label="Couple embracing in silhouette before the Eiffel Tower at sunset"></div>
    <div class="photo photo-relax" role="img" aria-label="The word Relax written in beach sand"></div>
    <div class="photo photo-beach" role="img" aria-label="Travellers resting in beach chairs under a blue sky"></div>
  </section>

  <section class="services-band">
    <div class="service">
      <svg class="service-icon" viewBox="0 0 150 70" aria-hidden="true">
        <path d="M30 46 Q32 24 55 22 L95 22 Q112 24 118 40 L124 46 Z" fill="var(--icon-tint)"/>
        <rect x="26" y="40" width="100" height="14" rx="6" fill="var(--icon-tint)"/>
        <circle cx="50" cy="56" r="9" fill="var(--band-green-dark)"/>
        <circle cx="104" cy="56" r="9" fill="var(--band-green-dark)"/>
        <path d="M56 28 L74 28 L74 40 L48 40 Q50 30 56 28 Z M80 28 L96 28 Q106 30 110 40 L80 40 Z" fill="var(--band-green)"/>
      </svg>
      <div class="service-title">PARK</div>
      <div class="service-note">leave your car at<br>the hotel</div>
    </div>
    <div class="service">
      <svg class="service-icon" viewBox="0 0 150 70" aria-hidden="true">
        <rect x="40" y="14" width="70" height="40" rx="4" fill="none" stroke="var(--icon-tint)" stroke-width="5"/>
        <rect x="50" y="22" width="20" height="10" rx="3" fill="var(--icon-tint)"/>
        <rect x="80" y="22" width="20" height="10" rx="3" fill="var(--icon-tint)"/>
        <rect x="40" y="38" width="70" height="6" fill="var(--icon-tint)"/>
        <rect x="40" y="54" width="6" height="8" fill="var(--icon-tint)"/>
        <rect x="104" y="54" width="6" height="8" fill="var(--icon-tint)"/>
      </svg>
      <div class="service-title">RELAX</div>
      <div class="service-note">start your vacation<br>a night early</div>
    </div>
    <div class="service">
      <svg class="service-icon" viewBox="0 0 150 70" aria-hidden="true">
        <path d="M20 36 L50 32 L62 14 L68 14 L62 32 L78 30 L84 24 L88 24 L86 34 L88 44 L84 44 L78 38 L62 38 L68 56 L62 56 L50 40 L20 38 Z" fill="var(--icon-tint)"/>
        <path d="M92 44 L140 44 L132 58 L98 58 Z" fill="var(--icon-tint)"/>
        <rect x="102" y="34" width="28" height="9" fill="var(--icon-tint)"/>
        <rect x="110" y="26" width="8" height="8" fill="var(--icon-tint)"/>
      </svg>
      <div class="service-title">SHUTTLE</div>
      <div class="service-note">transfers to the airport<br>or cruise port</div>
    </div>
    <div class="service">
      <svg class="service-icon" viewBox="0 0 150 70" aria-hidden="true">
        <path d="M48 24 Q75 2 104 24 Z" fill="var(--icon-tint)"/>
        <line x1="76" y1="16" x2="76" y2="62" stroke="var(--icon-tint)" stroke-width="4"/>
        <path d="M58 62 L66 40 L92 40 L98 62" fill="none" stroke="var(--icon-tint)" stroke-width="5"/>
        <line x1="62" y1="50" x2="96" y2="50" stroke="var(--icon-tint)" stroke-width="4"/>
      </svg>
      <div class="service-title">ENJOY!</div>
      <div class="service-note">have a worry<br>free vacation</div>
    </div>
  </section>

  <div class="rule"></div>

  <section class="offer">
    <div class="offer-headline">ENJOY $20 OFF A ONE NIGHT STAY</div>
    <div class="offer-sub">AT ANY OF OUR PROPERTIES</div>
    <div class="offer-terms">with this postcard *offer expires 12/31/16</div>
  </section>

  <div class="travel-graphic" role="img" aria-label="Illustration of hotel towers with palm trees and a globe"></div>
</main>
</body>
</html>
```